Bref créative
TradeCircle
Join the Sales & Marketing Community
Professional
Marta Zuccolin
Partner
Via Lentisco 7
20100 Milano
marta.zuccolin@tradecircle-example.it
www.tradecircle-example.it
Use the same design and colors of our winner logo in project "logo"

```html
<!DOCTYPE html>
<html lang="en">
<head>
<meta charset="utf-8">
<title>TradeCircle stationery</title>
<link href="https://fonts.googleapis.com/css2?family=Open+Sans:wght@400;600;700&display=swap" rel="stylesheet">
<style>
  :root{
    --board:#8e8e8e;
    --paper:#ffffff;
    --purple:#4f1a5c;
    --magenta:#a1195e;
    --orange:#f29a2e;
    --ink:#3a2a40;
    --muted:#8a8290;
    --caption:#d8d8d8;
  }
  *{margin:0;padding:0;box-sizing:border-box}
  html,body{width:1200px;height:338px;overflow:hidden;background:var(--board);font-family:"Open Sans",Arial,sans-serif}
  .board{position:relative;width:1200px;height:338px}
  .piece{position:absolute;background:var(--paper);overflow:hidden;box-shadow:0 2px 5px rgba(0,0,0,.35)}
  .piece svg.art{position:absolute;inset:0;width:100%;height:100%}
  .caption{position:absolute;font-size:5px;color:var(--caption);letter-spacing:.2px;white-space:nowrap}
  .brand{position:absolute;display:flex;align-items:center;gap:3px;font-weight:700;color:var(--magenta);white-space:nowrap}
  .brand .dot{border-radius:50%;background:var(--magenta)}
  .tagline{position:absolute;font-size:3px;color:var(--muted);white-space:nowrap}
  .contact{position:absolute;font-size:3px;line-height:4.2px;color:var(--ink);white-space:nowrap}
  .contact strong{font-weight:700;color:var(--purple)}
  .mark{position:absolute;border-radius:50%;background:var(--magenta);opacity:.07}
</style>
</head>
<body>
<div class="board">

  <svg width="0" height="0" style="position:absolute">
    <defs>
      <linearGradient id="band-purple" x1="0" y1="0" x2="1" y2="1">
        <stop offset="0" stop-color="#a1195e"/>
        <stop offset="1" stop-color="#4f1a5c"/>
      </linearGradient>
      <linearGradient id="band-orange" x1="0" y1="0" x2="1" y2="0">
        <stop offset="0" stop-color="#f6b24a"/>
        <stop offset="1" stop-color="#ee7f22"/>
      </linearGradient>
    </defs>
  </svg>

  <!-- Business card front -->
  <div class="piece card-front" style="left:29px;top:113px;width:77px;height:41px">
    <svg class="art" viewBox="0 0 77 41" preserveAspectRatio="none">
      <path d="M0 41 L0 34 C25 30 50 36 77 28 L77 41 Z" fill="url(#band-orange)"/>
      <path d="M0 41 L0 37 C25 33 50 39 77 32 L77 41 Z" fill="url(#band-purple)"/>
    </svg>
    <div class="brand" style="left:5px;top:5px;font-size:5px"><span class="dot" style="width:5px;height:5px"></span>TradeCircle</div>
    <div class="contact" style="left:5px;top:14px;font-size:2.6px;line-height:3.6px">
      <strong>Marta Zuccolin</strong><br>Partner<br>marta.zuccolin@tradecircle-example.it
    </div>
  </div>
  <div class="caption" style="left:29px;top:157px">Business card front</div>

  <!-- Business card back -->
  <div class="piece card-back" style="left:29px;top:178px;width:77px;height:41px">
    <svg class="art" viewBox="0 0 77 41" preserveAspectRatio="none">
      <path d="M0 0 L77 0 L77 8 C50 13 25 6 0 11 Z" fill="url(#band-purple)"/>
      <path d="M0 11 C25 6 50 13 77 8 L77 10 C50 15 25 8 0 13 Z" fill="url(#band-orange)"/>
    </svg>
    <div class="brand" style="left:20px;top:20px;font-size:5px"><span class="dot" style="width:5px;height:5px"></span>TradeCircle</div>
  </div>
  <div class="caption" style="left:29px;top:222px">Business card back</div>

  <!-- Letterhead -->
  <div class="piece letterhead" style="left:154px;top:17px;width:182px;height:288px">
    <svg class="art" viewBox="0 0 182 288" preserveAspectRatio="none">
      <path d="M160 0 C140 90 150 200 120 288 L182 288 L182 0 Z" fill="url(#band-orange)"/>
      <path d="M168 0 C150 90 160 200 132 288 L182 288 L182 0 Z" fill="url(#band-purple)"/>
    </svg>
    <div class="mark" style="left:40px;top:110px;width:70px;height:70px"></div>
    <div class="brand" style="left:12px;top:10px;font-size:7px"><span class="dot" style="width:7px;height:7px"></span>TradeCircle</div>
    <div class="tagline" style="left:22px;top:20px">Join the Sales &amp; Marketing Community</div>
    <div class="contact" style="left:12px;top:262px">
      Via Lentisco 7 · 20100 Milano<br>marta.zuccolin@tradecircle-example.it<br>www.tradecircle-example.it
    </div>
  </div>
  <div class="caption" style="left:154px;top:309px">Letterhead</div>

  <!-- Continuation sheet -->
  <div class="piece sheet" style="left:386px;top:17px;width:187px;height:288px">
    <svg class="art" viewBox="0 0 187 288" preserveAspectRatio="none">
      <path d="M0 288 L0 262 C60 250 120 268 187 226 L187 288 Z" fill="url(#band-orange)"/>
      <path d="M0 288 L0 270 C60 258 120 276 187 236 L187 288 Z" fill="url(#band-purple)"/>
    </svg>
    <div class="mark" style="left:58px;top:110px;width:70px;height:70px"></div>
    <div class="brand" style="left:12px;top:10px;font-size:7px"><span class="dot" style="width:7px;height:7px"></span>TradeCircle</div>
    <div class="tagline" style="left:22px;top:20px">Join the Sales &amp; Marketing Community</div>
  </div>
  <div class="caption" style="left:386px;top:309px">Continuation sheet</div>

  <!-- Envelope front -->
  <div class="piece envelope-front" style="left:624px;top:26px;width:214px;height:125px">
    <svg class="art" viewBox="0 0 214 125" preserveAspectRatio="none">
      <path d="M0 125 L0 100 C70 120 150 80 214 60 L214 125 Z" fill="url(#band-orange)"/>
      <path d="M0 125 L0 110 C70 128 150 90 214 72 L214 125 Z" fill="url(#band-purple)"/>
    </svg>
    <div class="brand" style="left:12px;top:10px;font-size:7px"><span class="dot" style="width:7px;height:7px"></span>TradeCircle</div>
    <div class="contact" style="left:12px;top:22px">Via Lentisco 7 · 20100 Milano</div>
  </div>
  <div class="caption" style="left:624px;top:154px">Envelope front</div>

  <!-- Envelope window -->
  <div class="piece envelope-window" style="left:624px;top:175px;width:214px;height:108px">
    <svg class="art" viewBox="0 0 214 108" preserveAspectRatio="none">
      <path d="M0 0 L214 0 L214 14 C140 30 60 4 0 26 Z" fill="url(#band-purple)"/>
      <path d="M0 26 C60 4 140 30 214 14 L214 19 C140 35 60 9 0 31 Z" fill="url(#band-orange)"/>
    </svg>
    <div class="brand" style="left:12px;top:38px;font-size:7px"><span class="dot" style="width:7px;height:7px"></span>TradeCircle</div>
    <div class="contact" style="left:12px;top:50px">www.tradecircle-example.it</div>
  </div>
  <div class="caption" style="left:624px;top:287px">Envelope window</div>

  <!-- Envelope back -->
  <div class="piece envelope-back" style="left:850px;top:38px;width:322px;height:245px;background:transparent;box-shadow:none">
    <svg class="art" viewBox="0 0 322 245" preserveAspectRatio="none">
      <path d="M0 74 L0 0 L322 0 L322 74 L161 112 Z" fill="url(#band-purple)"/>
      <path d="M0 0 L322 0 L322 30 C230 20 90 50 0 36 Z" fill="#a1195e" opacity=".6"/>
      <path d="M0 80 L322 80 L322 245 L0 245 Z" fill="#ffffff"/>
      <path d="M0 80 L161 170 L322 80" fill="none" stroke="#d6d6d6" stroke-width="1"/>
      <path d="M0 245 L130 150 M322 245 L192 150" stroke="#e2e2e2" stroke-width="1"/>
      <path d="M0 80 L0 74 L161 112 L322 74 L322 80 L161 120 Z" fill="url(#band-orange)"/>
    </svg>
    <div class="brand" style="left:139px;top:122px;font-size:6px"><span class="dot" style="width:6px;height:6px"></span>TradeCircle</div>
  </div>
  <div class="caption" style="left:850px;top:287px">Envelope back</div>

</div>
</body>
</html>
```